Social media agency for startUps! Need captivating web banner(s) needed

We need a few banners if Possible for a lead generation - branding campaign we are about to launch on Workvine & Chatterloop. We are Social media Agency created to help Startup and small medium business build there digital footprint. We also offer a brand analysing service to help brands understand there real time impact along with consulting, coaching and managed services. We are very open to the design concept. We are looking for creativity and professionalism. Something that will captivate and peek interest in learning more about how a company can work with us. We are need banners for Chatterloop and Workvine. If you require the formats please ask and we will send them. 2 for each platform would be nice, but depending on cost we would be happy with i for each network.

Designs should have our tag line : Accelerated Marketing. Refreshing Results. it should alsl speak to the fact that we are the Social Media Agency for Startups in Canada.

Target Market(s)

Small Medium Business and Start up companies

Industry/Entity Type

Media

Requirements
Must have
• company name - TrailMOSS Social
• out tag line - Accelerated Marketing. Refreshing Results
• our Logo -
• ad size -
• 160x600 Workvine
• 30x250 Workvine
• 1,200 x 628 pixels Chatterloop
• Recommended image size: 600 x 600 pixels
Nice to have
• This is the hard part - I would like to see something like a collage of all the social networks and how our brand connects them to the business in question. The other aspect could be something related to when you leveled up in a video game.
• i know this is somewhat vague, but i am open to any question you might have relating to this project.

```html
<!DOCTYPE html>
<html lang="en">
<head>
<meta charset="utf-8">
<title>TrailMOSS Social – Accelerated Marketing. Refreshing Results</title>
<link rel="stylesheet" href="https://fonts.googleapis.com/css2?family=Oswald:wght@400;500;600&family=Open+Sans:wght@400&display=swap">
<style>
  :root {
    --bg: #22222f;
    --orange: #f7941d;
    --orange-deep: #f15a24;
    --rise-warm: #8a4a22;
    --ink-light: #ffffff;
    --list-grey: #9c9ca8;
    --photo-light: #eef0f1;
    --photo-mid: #d3d8dc;
    --photo-dark: #a9b2b8;
  }
  html, body {
    margin: 0;
    padding: 0;
    overflow: hidden;
    background: var(--bg);
  }
  .banner {
    position: relative;
    width: 1200px;
    height: 628px;
    overflow: hidden;
    background: var(--bg);
    font-family: "Oswald", "Arial Narrow", sans-serif;
  }
  .brand {
    position: absolute;
    left: 30px;
    top: 40px;
    width: 380px;
    text-align: center;
    color: var(--ink-light);
  }
  .brand-mark {
    display: block;
    width: 64px;
    height: 64px;
    margin: 40px auto 34px;
    border-radius: 50%;
    background: var(--orange);
  }
  .brand-name {
    margin: 0;
    font-size: 37px;
    font-weight: 500;
    letter-spacing: 4px;
    line-height: 1;
    text-transform: uppercase;
  }
  .brand-tagline {
    margin: 5px 0 0;
    font-family: "Open Sans", Arial, sans-serif;
    font-size: 17px;
    letter-spacing: 0.4px;
  }
  .services {
    position: absolute;
    left: 36px;
    top: 290px;
    margin: 0;
    padding: 0;
    list-style: none;
    color: var(--list-grey);
    font-size: 28px;
    font-weight: 400;
    text-transform: uppercase;
    letter-spacing: 0.2px;
  }
  .services li {
    position: relative;
    padding-left: 32px;
    height: 57px;
    line-height: 42px;
  }
  .services li::before {
    content: "";
    position: absolute;
    left: 2px;
    top: 17px;
    width: 9px;
    height: 9px;
    border-radius: 50%;
    background: var(--list-grey);
  }
  .hero {
    position: absolute;
    left: 0;
    top: 0;
  }
  .tagline-diagonal {
    font-family: "Oswald", "Arial Narrow", sans-serif;
    font-weight: 500;
    font-size: 33px;
  }
  .tagline-accent { fill: var(--orange); }
  .tagline-light { fill: var(--ink-light); }
</style>
</head>
<body>
<div class="banner">

  <svg class="hero" width="1200" height="628" viewBox="0 0 1200 628">
    <defs>
      <linearGradient id="rise-glow" x1="0" y1="0" x2="0" y2="1">
        <stop offset="0" stop-color="var(--rise-warm)" stop-opacity="0.55"/>
        <stop offset="1" stop-color="var(--rise-warm)" stop-opacity="0"/>
      </linearGradient>
      <linearGradient id="photo-tone" x1="0" y1="0" x2="1" y2="1">
        <stop offset="0" stop-color="var(--photo-light)"/>
        <stop offset="0.6" stop-color="var(--photo-mid)"/>
        <stop offset="1" stop-color="var(--photo-dark)"/>
      </linearGradient>
      <linearGradient id="frame-tone" x1="0" y1="1" x2="1" y2="0">
        <stop offset="0" stop-color="var(--orange)"/>
        <stop offset="1" stop-color="var(--orange-deep)"/>
      </linearGradient>
    </defs>

    <rect class="rise-graphic" role="img" aria-label="Decorative rising arrows graphic"
          x="605" y="40" width="180" height="360" fill="url(#rise-glow)"/>

    <path role="img" aria-label="Photo of a desk from above with laptop, tablet, glasses and papers, overlaid with a marketing word cloud: sales, publicity, direct marketing, branding, strategy, marketing plan, public relations, advertising"
          d="M905,15 L1300,565 L1120,565 L1120,640 L695,640 L695,565 L510,565 Z"
          fill="url(#photo-tone)"/>
    <path class="frame-edge"
          d="M695,640 L695,565 L510,565 L905,15 L1300,565 L1120,565 L1120,640"
          fill="none" stroke="url(#frame-tone)" stroke-width="6" stroke-linejoin="miter"/>

    <text class="tagline-diagonal" transform="translate(490,550) rotate(-54.3)"
          textLength="640" lengthAdjust="spacingAndGlyphs">
      <tspan class="tagline-accent">ACCELERATED MARKETING.</tspan><tspan class="tagline-light"> REFRESHING RESULTS</tspan>
    </text>
  </svg>

  <header class="brand">
    <span class="brand-mark" aria-hidden="true"></span>
    <h1 class="brand-name">TrailMOSS Social</h1>
    <p class="brand-tagline">Accelerated Marketing. Refreshing results</p>
  </header>

  <ul class="services">
    <li>Brand Analysing Service</li>
    <li>Consulting</li>
    <li>Coaching &amp; Managed Services</li>
    <li>Online Marketing</li>
    <li>Social Media</li>
  </ul>

</div>
</body>
</html>
```